Vindgerdi - Start-up company selling electricity

Hello let me tell you about Vindgerdi.

Vindgerdi is start-up company selling electricity in Iceland. The operations of the company consist of making power usage forecasts for our customers, purchasing the electricity wholesale from the energy producers, and selling the electricity to the consumer. We are focused on tech by using optimization and machine learning to minimize electricity prices to our customers. Our marketing strategy is to portray a tech company mindset and to show dedication to driving down the electricity price on the market.

We need your help to make our website pop. Possible concepts to work with are as follows:

- Iceland the land of ice and fire
- Green energy
- Innovation
- Tech and data science

Link to our website: https://prufa.vindgerdi-example.is/
We are open to ideas.
Thank you!

Target Market(s)

Electricity consumers both homes and companies.

Number of Pages Required

1 page

Font styles to use
Serif
Sans Serif

```html
<!DOCTYPE html>
<html lang="en">
<head>
<meta charset="utf-8">
<title>Vindgerdi – Same electricity, just cheaper</title>
<link rel="stylesheet" href="https://fonts.googleapis.com/css2?family=Playfair+Display:wght@700;900&family=Lato:wght@400;700&display=swap">
<style>
  :root {
    --red: #a6332b;
    --navy: #1a3158;
    --ink: #1b1b1b;
    --muted: #666a70;
    --white: #ffffff;
    --serif: "Playfair Display", Georgia, serif;
    --sans: "Lato", Arial, sans-serif;
  }
  * { box-sizing: border-box; margin: 0; padding: 0; }
  html, body { width: 1200px; height: 2473px; overflow: hidden; }
  body { font-family: var(--sans); color: var(--ink); background: var(--white); position: relative; }

  /* Hero */
  .hero { position: relative; height: 600px; overflow: hidden; }
  .hero-scene {
    position: absolute; inset: 0;
    background:
      radial-gradient(ellipse 45% 30% at 55% 22%, rgba(236,90,50,.9), transparent 70%),
      linear-gradient(180deg, #2b4f9a 0%, #c5506a 22%, #e26b3f 36%, #5d6b2a 48%, #3f5a22 62%, #2f7fa8 78%, #2a4f4a 100%);
  }
  .nav { position: absolute; top: 0; left: 0; right: 0; height: 100px; display: flex; align-items: center; justify-content: space-between; padding: 0 62px 0 112px; }
  .brand { display: flex; align-items: center; gap: 10px; color: var(--white); font-family: var(--serif); font-weight: 700; font-size: 30px; letter-spacing: .5px; }
  .brand-dot { width: 26px; height: 26px; border-radius: 50%; background: var(--white); }
  .nav-links { display: flex; gap: 51px; list-style: none; }
  .nav-links a { color: var(--white); text-decoration: none; font-size: 16.5px; }
  .hero-title { position: absolute; top: 252px; left: 0; right: 0; text-align: center; color: var(--white); font-family: var(--serif); font-weight: 900; font-size: 46px; line-height: 51px; text-shadow: 0 2px 6px rgba(0,0,0,.3); }
  .hero-arrow { position: absolute; top: 278px; width: 24px; height: 44px; }
  .hero-arrow.prev { left: 54px; }
  .hero-arrow.next { right: 54px; }
  .hero-dots { position: absolute; top: 544px; left: 0; right: 0; display: flex; justify-content: center; gap: 7px; }
  .hero-dots span { width: 14px; height: 14px; border-radius: 50%; background: rgba(255,255,255,.5); }
  .hero-dots span.active { background: var(--white); }

  /* Section heads */
  .section-mark { width: 28px; height: 28px; border-radius: 50%; background: var(--navy); margin: 0 auto; }
  .section-title { font-family: var(--serif); font-weight: 900; font-size: 36px; text-align: center; color: var(--ink); letter-spacing: .3px; }

  /* Welcome */
  .welcome { height: 462px; padding-top: 690px; margin-top: -600px; }
  .welcome .section-mark { margin-top: 14px; }
  .welcome .section-title { margin-top: 22px; line-height: 44px; }
  .welcome-text { width: 860px; margin: 20px auto 0; text-align: center; font-size: 14.5px; line-height: 26.6px; color: var(--muted); letter-spacing: -.2px; }
  .actions { display: flex; justify-content: center; gap: 28px; margin-top: 31px; }
  .btn { display: inline-flex; align-items: center; justify-content: center; height: 46px; border-radius: 23px; color: var(--white); font-size: 18px; font-weight: 700; text-decoration: none; text-transform: uppercase; }
  .btn-red { background: var(--red); }
  .btn-navy { background: var(--navy); }
  .btn-wide { width: 169px; font-weight: 400; }

  /* Future band */
  .future { position: relative; height: 323px; margin-top: 0; overflow: hidden; top: 0; }
  .future-photo { position: absolute; left: 0; top: 0; width: 640px; height: 100%; background: linear-gradient(180deg, #5a6f86 0%, #8ea0ad 45%, #3b4f63 65%, #3e5a2c 100%); }
  .future-panel { position: absolute; left: 560px; top: 0; right: 0; height: 100%; background: var(--red); border-top-left-radius: 60% 100%; }
  .future-copy { position: absolute; left: 708px; top: 78px; width: 400px; color: var(--white); }
  .future-copy h2 { font-family: var(--serif); font-weight: 900; font-size: 35px; line-height: 37px; }
  .future-copy p { margin-top: 16px; font-size: 14.5px; line-height: 28.5px; letter-spacing: -.2px; }

  /* Price list */
  .prices { padding-top: 85px; }
  .prices .section-title { margin-top: 17px; line-height: 42px; }
  .price-grid { display: flex; justify-content: center; gap: 24px; margin-top: 15px; }
  .price-card { width: 467px; text-align: center; }
  .price-photo { height: 397px; }
  .photo-bulb { background: radial-gradient(circle at 48% 42%, #f4c35a 0%, #c7874a 18%, #6a6a6a 45%, #3a3a3a 100%); }
  .photo-wind { background: linear-gradient(180deg, #2c5f9e 0%, #7ea3cc 45%, #c9d7e6 65%, #8a7a5a 85%, #6b5a3c 100%); }
  .price { margin-top: 10px; font-size: 19px; color: #333; }
  .price strong { font-size: 34px; font-weight: 400; color: var(--ink); margin-right: 6px; }
  .price-action { display: flex; justify-content: center; margin-top: 28px; }
  .price-action .btn { width: 300px; }

  /* Footer */
  .footer { position: absolute; left: 0; right: 0; top: 2196px; bottom: 0; background: var(--navy); color: var(--white); }
  .footer .brand { justify-content: center; margin-top: 57px; font-size: 29px; }
  .footer-ids { display: flex; justify-content: center; gap: 24px; margin-top: 20px; font-size: 15px; }
  .footer-contact { display: flex; justify-content: center; gap: 22px; margin-top: 23px; font-size: 15px; }
  .footer-contact span { display: inline-flex; align-items: center; gap: 7px; }
  .footer-contact svg { width: 14px; height: 14px; fill: var(--white); }
  .footer-rule { position: absolute; left: 0; right: 0; top: 209px; border-top: 1px solid rgba(255,255,255,.3); }
  .copyright { position: absolute; left: 0; right: 0; top: 232px; text-align: center; font-size: 14px; }
  .to-top { position: absolute; right: 30px; top: 172px; width: 30px; height: 30px; }
</style>
</head>
<body>

<header class="hero">
  <div class="hero-scene" role="img" aria-label="Icelandic landscape at sunset with a waterfall, a conical mountain and a river"></div>
  <nav class="nav">
    <div class="brand"><span class="brand-dot"></span>VINDGERDI</div>
    <ul class="nav-links">
      <li><a href="#">Terms of business</a></li>
      <li><a href="#">Question &amp; Answer</a></li>
      <li><a href="#">About Vindgerdi</a></li>
    </ul>
  </nav>
  <h1 class="hero-title">SAME ELECTRICITY ~<br>JUST CHEAPER!</h1>
  <svg class="hero-arrow prev" viewBox="0 0 24 44"><path d="M22 2 2 22l20 20" fill="none" stroke="#fff" stroke-width="2"/></svg>
  <svg class="hero-arrow next" viewBox="0 0 24 44"><path d="M2 2l20 20L2 42" fill="none" stroke="#fff" stroke-width="2"/></svg>
  <div class="hero-dots"><span class="active"></span><span></span><span></span><span></span></div>
</header>

<section class="welcome" style="height:462px;padding-top:0;margin-top:0;">
  <div class="section-mark" style="margin-top:84px;"></div>
  <h2 class="section-title">WELCOME TO BUSINESS</h2>
  <p class="welcome-text">Vindgerdi is start-up company selling electricity in Iceland. The operations of the company consist of making power usage forecasts for our customers, purchasing the electricity wholesale from the energy producers, and selling the electricity to the consumer. We are focused on tech by using optimization and machine learning to minimize electricity prices to our customers. Our marketing strategy is to portray a tech company mindset and to show dedication to driving down the electricity price on the market.</p>
  <div class="actions">
    <a class="btn btn-red btn-wide" href="#">COMPANY</a>
    <a class="btn btn-navy btn-wide" href="#">HOME</a>
  </div>
</section>

<section class="future">
  <div class="future-photo" role="img" aria-label="City skyline behind a field of solar panels"></div>
  <div class="future-panel"></div>
  <div class="future-copy">
    <h2>THE FUTURE IS<br>EXCITING</h2>
    <p>Let's make the electricity system smarter together. Vindgerdi uses artificial intelligence, data science and automation to minimize costs and promote eccentricity</p>
  </div>
</section>

<section class="prices">
  <div class="section-mark"></div>
  <h2 class="section-title">PRICE LIST</h2>
  <div class="price-grid">
    <div class="price-card">
      <div class="price-photo photo-bulb" role="img" aria-label="Hand holding a glowing light bulb surrounded by gears"></div>
      <p class="price"><strong>6.95</strong>/ISK / kWh</p>
    </div>
    <div class="price-card">
      <div class="price-photo photo-wind" role="img" aria-label="Wind turbines on a hill under a blue cloudy sky"></div>
      <p class="price"><strong>6.22</strong>/ISK / kWh electric acceleration</p>
    </div>
  </div>
  <div class="price-action"><a class="btn btn-red" href="#" style="font-weight:400;">MAKE A PRICE COMPARISON</a></div>
</section>

<footer class="footer">
  <div class="brand"><span class="brand-dot"></span>VINDGERDI</div>
  <div class="footer-ids">
    <span>Vindgerdi ehf</span><span>ID number: 550118-0420</span><span>VAT number: 204731</span>
  </div>
  <div class="footer-contact">
    <span><svg viewBox="0 0 14 14"><path d="M7 0a4.5 4.5 0 0 0-4.5 4.5C2.5 8 7 14 7 14s4.5-6 4.5-9.5A4.5 4.5 0 0 0 7 0Zm0 6.3a1.8 1.8 0 1 1 0-3.6 1.8 1.8 0 0 1 0 3.6Z"/></svg>Lindarbraut 4 170 Bæjarnes</span>
    <span><svg viewBox="0 0 14 14"><path d="M0 3h14v1L7 8 0 4Zm0 2.3 7 4 7-4V12H0Z"/></svg>vindgerdi@vindgerdi-example.is</span>
    <span><svg viewBox="0 0 14 14"><path d="M3 0l2.5 3-1.4 1.8a8 8 0 0 0 5 5L11 8.5 14 11l-1.6 2.4C6.5 13.5.5 7.5.6 1.6Z"/></svg>555-0199</span>
  </div>
  <div class="footer-rule"></div>
  <p class="copyright">Copyright © Vindgerdi 2021 All rights reserved</p>
  <svg class="to-top" viewBox="0 0 30 30"><path d="M8 2h14l7 13-7 13H8L1 15Z" fill="none" stroke="#fff" stroke-width="2"/><path d="M15 8l-5 6h3v7h4v-7h3Z" fill="#fff"/></svg>
</footer>

</body>
</html>
```